Quorva - corporate Business Card

We need a good look and innovative business card for a new start up company based in Los Angeles called "Quorva". We are in a payment business, including payment card, app, and ewallet. We are expert in online payment and Card not present (CNP) transaction.
We need an innovative, modern business card.

Our logo font is Aero Matics

Target Market(s)

Startup - Bank - Online Payment - Card Manufacturing

Industry/Entity Type

Startup

Contact Information for Business Card

phone: 555 014 7396 - Address: 4172 Marlowe blvd, Fenwick Bay, OR 97999

Requirements
Must have
• Message: innovative, professional, expert, high tech, trust, online payment expert, security
Nice to have
• no comment
Should not have
• no Comment

```html
<!DOCTYPE html>
<html lang="en">
<head>
<meta charset="utf-8">
<title>Quorva – Business Card</title>
<link rel="stylesheet" href="https://fonts.googleapis.com/css2?family=Lato:wght@400;700;900&display=swap">
<style>
  :root {
    --brand-red: #b81d2e;
    --blush: #f6d3d6;
    --ink-grey: #6b6b6b;
    --paper: #ffffff;
    --backdrop: #dcdcde;
  }
  * { margin: 0; padding: 0; box-sizing: border-box; }
  html, body { width: 1200px; height: 900px; overflow: hidden; }
  body {
    background: var(--backdrop);
    font-family: "Lato", sans-serif;
    display: flex;
    align-items: center;
    justify-content: center;
    gap: 60px;
  }
  .card {
    position: relative;
    width: 520px;
    height: 300px;
    border-radius: 26px;
    overflow: hidden;
    box-shadow: 0 10px 24px rgba(0,0,0,0.14);
  }
  /* Front */
  .card--front { background: var(--paper); }
  .holder { position: absolute; left: 34px; top: 30px; }
  .holder__name {
    color: var(--brand-red);
    font-weight: 900;
    font-size: 15px;
    letter-spacing: 0.5px;
    text-transform: uppercase;
  }
  .holder__role { color: var(--ink-grey); font-size: 13px; margin-top: 2px; }
  .contacts {
    position: absolute; left: 34px; top: 118px;
    list-style: none;
    color: var(--ink-grey);
    font-size: 13.5px;
    line-height: 22px;
  }
  .contacts li { display: flex; align-items: center; gap: 8px; }
  .contacts svg { width: 11px; height: 11px; fill: var(--brand-red); flex: none; }
  .brand { position: absolute; display: flex; align-items: center; }
  .brand__dot { border-radius: 50%; flex: none; }
  .brand__name { font-weight: 700; line-height: 1; letter-spacing: 1px; }
  .card--front .brand { left: 238px; top: 106px; gap: 12px; }
  .card--front .brand__dot { width: 62px; height: 62px; background: var(--brand-red); }
  .card--front .brand__name { color: var(--brand-red); font-size: 54px; }
  .address-band {
    position: absolute; left: 0; right: 0; bottom: 0;
    height: 66px;
    background: var(--brand-red);
    color: var(--paper);
    font-size: 14.5px;
    display: flex; align-items: center;
    padding-left: 34px;
  }
  /* Back */
  .card--back { background: var(--brand-red); }
  .card--back .brand { left: 50%; top: 50%; transform: translate(-50%, -50%); gap: 14px; }
  .card--back .brand__dot { width: 72px; height: 72px; background: var(--blush); }
  .card--back .brand__name { color: var(--blush); font-size: 62px; }
</style>
</head>
<body>
  <section class="card card--front" aria-label="Business card front">
    <div class="holder">
      <p class="holder__name">Dorian Halvers</p>
      <p class="holder__role">Managing Director</p>
    </div>
    <ul class="contacts">
      <li>
        <svg viewBox="0 0 24 24" aria-hidden="true"><path d="M6.6 10.8a15.5 15.5 0 0 0 6.6 6.6l2.2-2.2a1 1 0 0 1 1-.25 11.4 11.4 0 0 0 3.6.57 1 1 0 0 1 1 1V20a1 1 0 0 1-1 1A17 17 0 0 1 3 4a1 1 0 0 1 1-1h3.5a1 1 0 0 1 1 1c0 1.25.2 2.45.57 3.57a1 1 0 0 1-.25 1z"/></svg>
        555 014 7396
      </li>
      <li>
        <svg viewBox="0 0 24 24" aria-hidden="true"><path d="M2 5h20v14H2z M2 5l10 8 10-8" /></svg>
        hello@quorvapay.com
      </li>
      <li>
        <svg viewBox="0 0 24 24" aria-hidden="true"><circle cx="12" cy="12" r="11"/></svg>
        www.quorvapay.com
      </li>
    </ul>
    <div class="brand">
      <span class="brand__dot"></span>
      <span class="brand__name">quorva</span>
    </div>
    <div class="address-band">4172 Marlowe blvd, Fenwick Bay, OR 97999</div>
  </section>

  <section class="card card--back" aria-label="Business card back">
    <div class="brand">
      <span class="brand__dot"></span>
      <span class="brand__name">quorva</span>
    </div>
  </section>
</body>
</html>
```